KLV Plant Services

We are a heavy diesel mechanical business with additional air con certificates, remapping engine rebuilt

Contact Information for Business Card

Company Name, Director Name, Managing Director, Contact details, email and website

Font styles to use
Serif
Script

```html
<!DOCTYPE html>
<html lang="en">
<head>
<meta charset="utf-8">
<title>KLV Plant Services – Business Card</title>
<link href="https://fonts.googleapis.com/css2?family=Arimo:wght@400;700&display=swap" rel="stylesheet">
<style>
  :root {
    --stage: #d6d6d6;
    --navy: #06065a;
    --ink-white: #ffffff;
    --card-black: #030303;
    --silver: #8a8a8a;
    --rule: rgba(255,255,255,0.75);
  }
  * { box-sizing: border-box; margin: 0; padding: 0; }
  html, body { width: 1200px; height: 800px; overflow: hidden; }
  body {
    background: var(--stage);
    font-family: "Arimo", Arial, sans-serif;
    display: flex;
    align-items: center;
    justify-content: center;
    gap: 50px;
  }
  .card {
    position: relative;
    width: 530px;
    height: 310px;
    border-radius: 22px;
    overflow: hidden;
    box-shadow: 0 12px 28px rgba(0,0,0,0.28);
  }
  /* Front */
  .card-front { background: var(--navy); color: var(--ink-white); }
  .brand {
    position: absolute;
    display: flex;
    align-items: center;
    gap: 10px;
    font-weight: 700;
    white-space: nowrap;
  }
  .brand-dot {
    border-radius: 50%;
    border: 3px solid currentColor;
    flex: none;
  }
  .card-front .brand { top: 46px; right: 40px; font-size: 24px; }
  .card-front .brand-dot { width: 30px; height: 30px; }
  .holder { position: absolute; left: 34px; top: 152px; }
  .holder-name { font-size: 22px; font-weight: 700; }
  .holder-role { font-size: 14px; margin-top: 2px; }
  .divider {
    position: absolute; left: 34px; right: 34px; top: 200px;
    height: 1px; background: var(--rule);
  }
  .contacts { position: absolute; left: 34px; top: 212px; list-style: none; font-size: 13.5px; line-height: 1.45; }
  .contacts li { display: flex; align-items: center; gap: 8px; }
  .contacts svg { width: 11px; height: 11px; fill: var(--ink-white); flex: none; }
  .address { position: absolute; right: 38px; top: 214px; font-size: 14px; line-height: 1.5; text-align: left; }
  .edge-band { position: absolute; left: 0; right: 0; bottom: 0; height: 16px; display: flex; }
  .edge-band .band-light { flex: 0 0 64%; background: var(--ink-white); }
  .edge-band .band-dark { flex: 1; background: var(--card-black); }
  /* Back */
  .card-back { background: var(--card-black); color: var(--silver); }
  .card-back .brand { top: 50%; left: 50%; transform: translate(-50%, -50%); font-size: 34px; }
  .card-back .brand-dot { width: 44px; height: 44px; }
</style>
</head>
<body>
  <article class="card card-front">
    <div class="brand"><span class="brand-dot"></span><span class="brand-name">KLV Plant Services</span></div>
    <div class="holder">
      <p class="holder-name">Daniel Harlow</p>
      <p class="holder-role">Managing Director</p>
    </div>
    <div class="divider"></div>
    <ul class="contacts">
      <li><svg viewBox="0 0 24 24"><path d="M6.6 10.8a15.1 15.1 0 0 0 6.6 6.6l2.2-2.2a1 1 0 0 1 1-.25 11.4 11.4 0 0 0 3.6.57 1 1 0 0 1 1 1V20a1 1 0 0 1-1 1A17 17 0 0 1 3 4a1 1 0 0 1 1-1h3.5a1 1 0 0 1 1 1c0 1.25.2 2.45.57 3.6a1 1 0 0 1-.25 1z"/></svg>(555) 2190-4786</li>
      <li><svg viewBox="0 0 24 24"><path d="M2 5h20v14H2zm2 2v.5l8 5 8-5V7z"/></svg>name@KLV.com</li>
      <li><svg viewBox="0 0 24 24"><circle cx="12" cy="12" r="10"/></svg>www.KLV.com</li>
    </ul>
    <address class="address" style="font-style:normal">4127 Ashford Lane<br>Brookfield, NY 10990</address>
    <div class="edge-band"><span class="band-light"></span><span class="band-dark"></span></div>
  </article>

  <article class="card card-back">
    <div class="brand"><span class="brand-dot"></span><span class="brand-name">KLV Plant Services</span></div>
  </article>
</body>
</html>
```